Branding Pack for new business to business cost saving site

I would like a branding pack for my new project. I would like the following designed;
a4 Presentation folder
Letterhead
Envelope
Business Card
compliment splip

We are a business cost saving site, we have access to 1000s of discount offers for daily business to business offers. I already have the logo therfore please follow th e logo for the coloutr and design.

Target Market(s)

SMEs in United Kingdom

Industry/Entity Type

Business Service

Font styles to use
Serif
Script

Colors
0255a3
fbee3d

Requirements
Must have
• The folder needs to be the same size as attached

```html
<!DOCTYPE html>
<html lang="en">
<head>
<meta charset="utf-8">
<title>thriftwise stationery</title>
<link href="https://fonts.googleapis.com/css2?family=Arimo:wght@400;700&display=swap" rel="stylesheet">
<style>
  :root {
    --navy: #33367a;
    --navy-deep: #2c2f6e;
    --yellow: #ecc94a;
    --paper: #fbfbfb;
    --ink: #3a3a3a;
    --ground: #dcdcde;
    --white: #ffffff;
  }
  * { margin: 0; padding: 0; box-sizing: border-box; }
  html, body { width: 1200px; height: 991px; overflow: hidden; }
  body {
    background: var(--ground);
    position: relative;
    font-family: "Arimo", Arial, sans-serif;
    color: var(--ink);
  }
  .sheet { position: absolute; background: var(--paper); }
  .sheet.dark { background: var(--navy); }

  /* company name */
  .company-name {
    position: absolute;
    font-family: "Arimo", Arial, sans-serif;
    font-weight: 400;
    color: var(--navy);
    line-height: 1;
    white-space: nowrap;
  }
  .dark .company-name, .flap .company-name { color: var(--white); }
  .centered { left: 0; right: 0; text-align: center; }

  .band { position: absolute; left: 0; bottom: 0; width: 100%; display: block; }

  .contact { position: absolute; font-size: 5.6px; line-height: 7.4px; color: var(--ink); }
  .contact.ruled { border-left: 1.5px solid var(--navy); padding-left: 5px; }
  .contact .row { display: flex; align-items: center; gap: 3px; }
  .contact svg { width: 5px; height: 5px; flex: none; }
  .contact .gap { height: 3px; }

  /* letterhead */
  .letterhead { left: 71px; top: 104px; width: 398px; height: 560px; }
  .letterhead .company-name { left: 34px; top: 37px; font-size: 23px; }
  .letterhead .contact { left: 301px; top: 32px; }
  .letter {
    position: absolute; left: 35px; top: 152px; width: 330px;
    font-size: 5.2px; line-height: 7.2px; color: var(--ink);
  }
  .letter .date { margin-bottom: 10px; }
  .letter .recipient { margin-bottom: 40px; }
  .letter .salutation { margin-bottom: 7px; }
  .letter p.body { margin-bottom: 7px; text-align: justify; }
  .letter .closing { margin-top: 10px; }

  /* folder */
  .folder { left: 507px; top: 90px; width: 432px; height: 574px; border-radius: 3px; background: linear-gradient(160deg, #3b3f85 0%, var(--navy) 45%, var(--navy-deep) 100%); }
  .folder .spine { position: absolute; left: 0; top: 0; width: 26px; height: 100%; border-right: 1px solid rgba(0,0,0,0.15); }
  .folder .company-name { top: 88px; font-size: 42px; padding-left: 26px; }
  .folder .url { position: absolute; left: 26px; right: 0; top: 541px; text-align: center; color: var(--white); font-size: 8px; }

  /* business cards */
  .card-front { left: 66px; top: 696px; width: 170px; height: 94px; }
  .card-front .person { position: absolute; left: 13px; top: 23px; }
  .card-front .person .who { font-size: 5px; font-weight: 700; color: var(--navy); letter-spacing: 0.02em; }
  .card-front .person .role { font-size: 3.6px; color: var(--ink); margin-top: 1px; }
  .card-front .company-name { right: 12px; top: 20px; font-size: 14px; }
  .card-front .contact { left: 13px; top: 65px; font-size: 3.8px; line-height: 5.2px; }
  .card-front .contact svg { width: 3.6px; height: 3.6px; }
  .card-front .address { position: absolute; right: 12px; top: 71px; font-size: 3.8px; line-height: 5px; text-align: right; }
  .card-back { left: 66px; top: 810px; width: 170px; height: 94px; }
  .card-back .company-name { top: 38px; font-size: 18px; }
  .card-back .url { position: absolute; left: 0; right: 0; top: 80px; text-align: center; color: var(--white); font-size: 3.8px; }

  /* compliment slip */
  .slip { left: 266px; top: 696px; width: 415px; height: 208px; }
  .slip .company-name { left: 26px; top: 32px; font-size: 24px; }
  .slip .contact { left: 26px; top: 176px; }

  /* envelope */
  .envelope { left: 718px; top: 696px; width: 415px; height: 208px; }
  .envelope .flap { position: absolute; left: 0; top: 0; width: 415px; height: 60px; }
  .envelope .flap svg { position: absolute; inset: 0; }
  .envelope .company-name { top: 26px; font-size: 14px; }
</style>
</head>
<body>

<!-- Letterhead -->
<section class="sheet letterhead" aria-label="Letterhead">
  <div class="company-name">thriftwise</div>
  <div class="contact ruled">
    <div>Suite 2, 14 Harlow Road</div>
    <div>Leeds LS1 4AB</div>
    <div class="gap"></div>
    <div class="row"><svg viewBox="0 0 10 10"><path d="M2 1l2 2-1 1.5c.8 1.6 1.9 2.7 3.5 3.5L8 7l2 2-1.5 1C4.5 9.5.5 5.5 0 1.5z" fill="var(--navy)"/></svg>+44 20 7946 0321</div>
    <div class="row"><svg viewBox="0 0 10 10"><rect x="0.5" y="2" width="9" height="6" fill="var(--navy)"/><path d="M0.5 2l4.5 3.5L9.5 2" stroke="#fff" fill="none" stroke-width="0.8"/></svg>hello@thriftwise.co</div>
    <div class="row"><svg viewBox="0 0 10 10"><circle cx="5" cy="5" r="4.3" fill="none" stroke="var(--navy)" stroke-width="1"/><ellipse cx="5" cy="5" rx="1.8" ry="4.3" fill="none" stroke="var(--navy)" stroke-width="0.8"/><path d="M0.7 5h8.6" stroke="var(--navy)" stroke-width="0.8"/></svg>www.thriftwise.co</div>
  </div>
  <div class="letter">
    <div class="date">30.09.2018</div>
    <div class="recipient">Recipient's name<br>22 Orchard Lane<br>Bristol BS8 1QT<br>United Kingdom</div>
    <div class="salutation">Dear sir,</div>
    <p class="body">Thank you for your interest in our savings service. We work with thousands of suppliers to bring small and medium businesses lower prices on the things they buy every day, from office supplies and energy to travel, software and fleet costs. This letter sets out how we can help your team.</p>
    <p class="body">Membership is free for your first year. Once you join, you gain access to a members area with current offers sorted by category, a simple tool to compare your existing contracts against our rates, and a named account manager who reviews your spending twice a year and suggests where you could save.</p>
    <p class="body">Most of our members recover the cost of switching within three months. We handle the paperwork with each supplier, so your staff can stay focused on running the business.</p>
    <p class="body">If you would like to talk through your options, please reply to this letter or call us on the number above. We look forward to working with you.</p>
    <div class="closing">Yours Sincerely,<br>Noel Pettifer</div>
  </div>
  <svg class="band" viewBox="0 0 398 6" height="6" preserveAspectRatio="none"><polygon points="0,0 284,0 279,6 0,6" fill="var(--navy)"/><polygon points="289,0 398,0 398,6 282,6" fill="var(--yellow)"/></svg>
</section>

<!-- Presentation folder -->
<section class="sheet dark folder" aria-label="Presentation folder">
  <div class="spine"></div>
  <div class="company-name centered">thriftwise</div>
  <div class="url">www.thriftwise.co</div>
</section>

<!-- Business card front -->
<section class="sheet card-front" aria-label="Business card front">
  <div class="person"><div class="who">JAMIE CORRICK</div><div class="role">Director</div></div>
  <div class="company-name">thriftwise</div>
  <div class="contact">
    <div class="row"><svg viewBox="0 0 10 10"><path d="M2 1l2 2-1 1.5c.8 1.6 1.9 2.7 3.5 3.5L8 7l2 2-1.5 1C4.5 9.5.5 5.5 0 1.5z" fill="var(--navy)"/></svg>+44 20 7946 0321</div>
    <div class="row"><svg viewBox="0 0 10 10"><rect x="0.5" y="2" width="9" height="6" fill="var(--navy)"/></svg>hello@thriftwise.co</div>
    <div class="row"><svg viewBox="0 0 10 10"><circle cx="5" cy="5" r="4.3" fill="none" stroke="var(--navy)" stroke-width="1"/></svg>www.thriftwise.co</div>
  </div>
  <div class="address">Suite 2, 14 Harlow Road<br>Leeds LS1 4AB</div>
  <svg class="band" viewBox="0 0 170 3" height="3" preserveAspectRatio="none"><polygon points="0,0 106,0 103,3 0,3" fill="var(--navy)"/><polygon points="110,0 170,0 170,3 106,3" fill="var(--yellow)"/></svg>
</section>

<!-- Business card back -->
<section class="sheet dark card-back" aria-label="Business card back">
  <div class="company-name centered">thriftwise</div>
  <div class="url">www.thriftwise.co</div>
</section>

<!-- Compliment slip -->
<section class="sheet slip" aria-label="Compliment slip">
  <div class="company-name">thriftwise</div>
  <div class="contact ruled">
    <div>Suite 2, 14 Harlow Road</div>
    <div>Leeds LS1 4AB</div>
  </div>
  <svg class="band" viewBox="0 0 415 6" height="6" preserveAspectRatio="none"><polygon points="0,0 299,0 294,6 0,6" fill="var(--navy)"/><polygon points="304,0 415,0 415,6 297,6" fill="var(--yellow)"/></svg>
</section>

<!-- Envelope -->
<section class="sheet envelope" aria-label="Envelope">
  <div class="flap">
    <svg viewBox="0 0 415 60" width="415" height="60"><polygon points="0,0 415,0 400,60 15,60" fill="var(--navy)"/></svg>
    <div class="company-name centered">thriftwise</div>
  </div>
</section>

</body>
</html>
```